my website is tavorinque.com. (brand name is ta belle vitrine) This is just a template that i have choose for. The content and the pictures are not about my business just the template.
I would like to have 4 pages for now. 1 homepage, which will be an overview for all pages, it is right now in this way. It will directly highlight my story. My website will tell an exclusive story about details which makes the difference and will make people happy with very small things. It will be art related but very stylish as well. I also want to have a event agenda on my homepage where people can see where my next event is. Page 2 my blog, where I will write weekly about mindset, lifestyle and details. Inspiration place for people who are looking for unique and exclusive approaches in life. Page 3 shop, where I will sell my stuff which is handmade and unique, it will be limited edition stuff. Mostly I will make the designs from marbling art, which I am a teacher for. (https://www.vidoranta.com/watch?v=KpwuzRaxTmo) check this video out for more. Page 4 is book page. Here people will be able to book private or group classes for marbling art (check the video). I have already a community of more than 500 people on gath rix, which will be my public as well. I wanna implement the gath rix button on this page as well. to be able to track.

This is about my website. I also need a logo for my brand, which will suit my website and my goals.

I can also give you a reference website, which really like as structure and style;
https://www.brightorvalco.com/products/the-morning-ledger?gclid=Xr4TpLmwq2HsVD9KEBsZTrc-WkPhyQ-uvlEjdRs3NKaOYFCBWMpuTzG8xyCVbhdnLWRqoaNf_2e8ZtpRvHbAwq9FLQ_hqgQ

Logo Text

ta belle vitrine

Coding

Coded - Design and coding required

Number of Pages Required

4 page

Requirements
Must have
• I can also give you a reference website, which really like as structure and style;
• https://www.brightorvalco.com/products/the-morning-ledger?gclid=Xr4TpLmwq2HsVD9KEBsZTrc-WkPhyQ-uvlEjdRs3NKaOYFCBWMpuTzG8xyCVbhdnLWRqoaNf_2e8ZtpRvHbAwq9FLQ_hqgQ

```html
<!DOCTYPE html>
<html lang="en">
<head>
<meta charset="utf-8">
<title>ta belle vitrine</title>
<link href="https://fonts.googleapis.com/css2?family=Josefin+Sans:wght@400;600&family=Open+Sans:wght@400;600;700&display=swap" rel="stylesheet">
<style>
:root{
  --ink:#1f1f1f;
  --body:#6f6f6f;
  --accent:#c9a2a4;
  --accent-soft:#d5b6b7;
  --band:#c8a2a4;
  --footer:#676767;
  --footer-line:#7d7d7d;
  --white:#ffffff;
  --rule:#d9d9d9;
}
*{margin:0;padding:0;box-sizing:border-box}
html,body{width:1200px;height:3103px;overflow:hidden;background:var(--white)}
body{position:relative;font-family:"Open Sans",sans-serif;color:var(--body)}
.abs{position:absolute}
.display{font-family:"Josefin Sans",sans-serif;color:var(--ink);font-weight:600}

/* header */
.site-header{left:0;top:0;width:1200px;height:87px;background:var(--white)}
.brand{left:99px;top:22px;display:flex;align-items:center;gap:14px}
.brand-mark{width:40px;height:40px;border:2px solid var(--ink);border-radius:50%}
.brand-name{font-family:"Josefin Sans",sans-serif;font-size:26px;font-weight:400;color:var(--ink)}
.main-nav a{position:absolute;top:34px;font-family:"Josefin Sans",sans-serif;font-size:15px;font-weight:600;color:var(--ink);text-decoration:none;white-space:nowrap}
.main-nav a.current{color:var(--accent)}
.tool{top:24px;width:38px;height:38px;border:1.5px solid #bbb;border-radius:50%;display:flex;align-items:center;justify-content:center}
.tool.cart{background:var(--accent-soft);border-color:var(--accent-soft)}

/* hero */
.hero{left:0;top:87px;width:1200px;height:439px;background:linear-gradient(135deg,#4a4540 0%,#2b2826 45%,#5a534c 100%)}
.hero-title{left:0;width:1200px;top:208px;text-align:center;font-family:"Josefin Sans",sans-serif;font-weight:600;font-size:60px;letter-spacing:8px;color:var(--white)}
.hero-sub{left:0;width:1200px;top:285px;text-align:center;font-size:20px;line-height:34px;color:var(--white)}
.dots{left:574px;top:460px;display:flex;gap:4px}
.dots span{width:11px;height:11px;border:1.5px solid var(--white);border-radius:50%}
.dots span.on{background:var(--white)}

/* story */
.story-frame{left:223px;top:617px;width:373px;height:395px;border:1.5px solid #444}
.story-photo{left:99px;top:658px;width:460px;height:391px;background:linear-gradient(160deg,#5b5350 0%,#8a5a45 45%,#7a4a3a 100%)}
.section-title{font-size:34px}
.story-title{left:658px;top:642px}
.story-text{left:658px;top:708px;width:400px;font-size:13.5px;line-height:29px}
.btn{display:flex;align-items:center;justify-content:center;background:var(--accent-soft);color:var(--white);font-size:12px;font-weight:700;letter-spacing:.5px}
.story-btn{left:660px;top:954px;width:114px;height:35px}

/* services band */
.services{left:0;top:1134px;width:1200px;height:488px;background:radial-gradient(ellipse at 30% 40%,#d3b1b3 0%,#c59ea0 60%,#bd9496 100%)}
.services-title{left:0;width:1200px;top:1196px;text-align:center;color:var(--white);font-weight:400}
.service{top:1281px;width:240px;text-align:center;color:var(--white)}
.service .ring{width:148px;height:148px;margin:0 auto;border:2.5px solid var(--white);border-radius:50%;display:flex;align-items:center;justify-content:center}
.service h3{font-family:"Josefin Sans",sans-serif;font-weight:400;font-size:20px;margin-top:20px}
.service p{font-size:13px;line-height:24px;margin-top:6px;opacity:.9}
.service .more{font-size:11px;font-weight:700;margin-top:6px}

/* products */
.center-title{left:0;width:1200px;text-align:center}
.arrow{width:36px;height:36px;border:1.5px solid #cfcfcf;border-radius:50%;display:flex;align-items:center;justify-content:center}
.product{top:1786px;width:238px}
.product .pic{height:231px}
.product h4{font-family:"Josefin Sans",sans-serif;font-size:18px;font-weight:600;color:var(--ink);margin-top:22px}
.product .price{font-size:17px;color:var(--accent);margin-top:8px}
.divider{left:99px;top:2162px;width:1002px;height:2px;background:var(--rule)}

/* events */
.event{top:2303px;width:323px}
.event .pic{height:184px}
.event h4{font-family:"Josefin Sans",sans-serif;font-size:20px;font-weight:600;color:var(--ink);margin-top:32px}
.event .meta{font-size:13px;margin-top:12px;display:flex;align-items:center;gap:6px}
.event .meta svg{flex:none}
.event p{font-size:13px;line-height:25px;margin-top:12px}
.event .more{font-size:12px;font-weight:700;color:var(--accent);margin-top:16px;letter-spacing:.5px}

/* footer */
.site-footer{left:0;top:2741px;width:1200px;height:362px;background:var(--footer);color:var(--white)}
.foot-col{top:2800px}
.foot-col h5{font-family:"Josefin Sans",sans-serif;font-weight:400;font-size:17px;margin-bottom:14px}
.foot-col li{list-style:none;font-size:11.5px;line-height:27.5px}
.vrule{top:2795px;width:1px;height:190px;background:var(--footer-line)}
.sub-text{font-size:11.5px;margin-top:-2px}
.sub-form{top:2876px;left:778px;display:flex}
.sub-form .field{width:230px;height:34px;background:var(--white);color:#999;font-size:11px;padding:0 12px;display:flex;align-items:center}
.sub-form .go{width:93px;height:34px;background:var(--accent-soft);color:var(--white);font-size:11px;font-weight:700;display:flex;align-items:center;justify-content:center}
.stay{left:778px;top:2926px;font-family:"Josefin Sans",sans-serif;font-size:17px}
.socials{left:774px;top:2965px;display:flex;gap:10px}
.socials span{width:32px;height:32px;border-radius:50%;background:var(--accent-soft)}
.foot-rule{left:0;top:3031px;width:1200px;height:1px;background:var(--footer-line)}
.copy{left:0;width:1200px;top:3054px;text-align:center;font-size:11.5px}
</style>
</head>
<body>

<header class="abs site-header">
  <div class="abs brand"><span class="brand-mark"></span><span class="brand-name">ta belle vitrine</span></div>
  <nav class="main-nav">
    <a class="current" style="left:592px">HOME</a>
    <a style="left:678px">MY BLOG</a>
    <a style="left:783px">SHOP</a>
    <a style="left:863px">BOOK</a>
  </nav>
  <div class="abs tool" style="left:962px"><svg width="14" height="14" viewBox="0 0 14 14"><circle cx="6" cy="6" r="4.2" fill="none" stroke="#333" stroke-width="1.8"/><path d="M9 9l3.5 3.5" stroke="#333" stroke-width="1.8"/></svg></div>
  <div class="abs tool" style="left:1010px"><svg width="12" height="14" viewBox="0 0 12 14"><circle cx="6" cy="4" r="3" fill="#333"/><path d="M0 14c0-4 2.5-6 6-6s6 2 6 6z" fill="#333"/></svg></div>
  <div class="abs tool cart" style="left:1061px"><svg width="15" height="14" viewBox="0 0 15 14"><path d="M0 1h3l2 8h8l2-6H4" fill="none" stroke="#fff" stroke-width="1.6"/><circle cx="6" cy="12" r="1.3" fill="#fff"/><circle cx="12" cy="12" r="1.3" fill="#fff"/></svg></div>
</header>

<section class="abs hero" role="img" aria-label="Marbling tray with paint jars on a studio table"></section>
<h1 class="abs hero-title">TA BELLE VITRINE</h1>
<p class="abs hero-sub">ta belle vitrine is a trendsetting Online Store,<br>offering our first-rate products</p>
<div class="abs dots"><span class="on"></span><span></span><span></span><span></span></div>

<div class="abs story-frame"></div>
<div class="abs story-photo" role="img" aria-label="Marbling bath with floating colours and paint jars"></div>
<h2 class="abs display section-title story-title">MY STORY</h2>
<p class="abs story-text">ta belle vitrine is a leading Online Store. We provide an unparalleled selection of the very best quality products, an easy and comfortable shopping experience, expedited shipping offers, and exceptional customer service. Check out our collection of new arrivals, best-sellers, and clearance items today. ta belle vitrine is a trendsetting Online Store, offering our first-rate products and exceptional customer service to shoppers from the comfort of their own homes.</p>
<div class="abs btn story-btn">READ MORE</div>

<section class="abs services" role="img" aria-label="Soft pink marbled paper background"></section>
<h2 class="abs display section-title services-title">WHAT WE DO</h2>

<div class="abs service" style="left:89px">
  <div class="ring"><svg width="64" height="64" viewBox="0 0 64 64"><path d="M46 8a14 14 0 0 0-16 18L10 46a5 5 0 0 0 8 8l20-20a14 14 0 0 0 18-16l-8 8-7-2-2-7z" fill="#fff"/></svg></div>
  <h3>Template service</h3>
  <p>We provide an unparalleled selection<br>of the very best quality products</p>
  <div class="more">READ MORE &gt;&gt;</div>
</div>
<div class="abs service" style="left:352px">
  <div class="ring"><svg width="70" height="64" viewBox="0 0 70 64"><circle cx="24" cy="30" r="15" fill="none" stroke="#fff" stroke-width="9" stroke-dasharray="6 4"/><circle cx="24" cy="30" r="6" fill="#fff"/><circle cx="52" cy="16" r="8" fill="none" stroke="#fff" stroke-width="6" stroke-dasharray="4 3"/><circle cx="52" cy="46" r="8" fill="none" stroke="#fff" stroke-width="6" stroke-dasharray="4 3"/></svg></div>
  <h3>Cut and process</h3>
  <p>We provide an unparalleled selection<br>of the very best quality products</p>
  <div class="more">READ MORE &gt;&gt;</div>
</div>
<div class="abs service" style="left:612px">
  <div class="ring"><svg width="72" height="52" viewBox="0 0 72 52"><rect x="2" y="4" width="42" height="32" fill="#fff"/><path d="M46 14h14l10 12v10H46z" fill="#fff"/><circle cx="16" cy="42" r="7" fill="#fff" stroke="#c8a2a4" stroke-width="3"/><circle cx="56" cy="42" r="7" fill="#fff" stroke="#c8a2a4" stroke-width="3"/></svg></div>
  <h3>Delivery and Fit</h3>
  <p>We provide an unparalleled selection<br>of the very best quality products</p>
  <div class="more">READ MORE &gt;&gt;</div>
</div>
<div class="abs service" style="left:871px">
  <div class="ring"><svg width="60" height="60" viewBox="0 0 60 60"><path d="M10 26A20 20 0 0 1 46 16" fill="none" stroke="#fff" stroke-width="8"/><path d="M52 6v18H34z" fill="#fff"/><path d="M50 34A20 20 0 0 1 14 44" fill="none" stroke="#fff" stroke-width="8"/><path d="M8 54V36h18z" fill="#fff"/></svg></div>
  <h3>Floor renovation</h3>
  <p>We provide an unparalleled selection<br>of the very best quality products</p>
  <div class="more">READ MORE &gt;&gt;</div>
</div>

<h2 class="abs display section-title center-title" style="top:1712px">OUR PRODUCTS</h2>
<div class="abs arrow" style="left:50px;top:1881px"><svg width="10" height="14" viewBox="0 0 10 14"><path d="M8 1L2 7l6 6" fill="none" stroke="#999" stroke-width="2"/></svg></div>
<div class="abs arrow" style="left:1116px;top:1881px"><svg width="10" height="14" viewBox="0 0 10 14"><path d="M2 1l6 6-6 6" fill="none" stroke="#999" stroke-width="2"/></svg></div>

<div class="abs product" style="left:99px"><div class="pic" role="img" aria-label="Turquoise and white marbled paper" style="background:linear-gradient(135deg,#7fcbd6,#e9f4f4 50%,#3d9fb5)"></div><h4>Finibus Bonoruet Maloru</h4><div class="price">$34.00</div></div>
<div class="abs product" style="left:354px"><div class="pic" role="img" aria-label="Marbled paper with pink flowers on green" style="background:linear-gradient(135deg,#8fb6a0,#e59ea6 50%,#6f9a72)"></div><h4>Finibus Bonoruet Maloru</h4><div class="price">$34.00</div></div>
<div class="abs product" style="left:608px"><div class="pic" role="img" aria-label="Brown marbled paper with white veins" style="background:linear-gradient(135deg,#8d5a48,#b08a7e 50%,#7a4a3a)"></div><h4>Finibus Bonoruet Maloru</h4><div class="price">$34.00</div></div>
<div class="abs product" style="left:863px"><div class="pic" role="img" aria-label="Purple and brown marbled paper" style="background:linear-gradient(135deg,#8a6d86,#c4aac0 50%,#5e3f48)"></div><h4>Finibus Bonoruet Maloru</h4><div class="price">$34.00</div></div>

<div class="abs divider"></div>

<h2 class="abs display section-title center-title" style="top:2226px">LATEST EVENTS</h2>

<div class="abs event" style="left:99px">
  <div class="pic" role="img" aria-label="Hand placing ceramic dishes on a table" style="background:linear-gradient(135deg,#6b6965,#9d9a95 60%,#c7c3bd)"></div>
  <h4>Finibus Bonorumet Maloru</h4>
  <div class="meta"><svg width="12" height="12" viewBox="0 0 12 12"><rect x="1" y="2" width="10" height="9" fill="none" stroke="#c9a2a4" stroke-width="1.4"/><path d="M1 5h10" stroke="#c9a2a4"/></svg>25/09/2017 &nbsp;| &nbsp;<svg width="11" height="12" viewBox="0 0 11 12"><circle cx="5.5" cy="3.5" r="2.8" fill="#c9a2a4"/><path d="M0 12c0-4 2-5.5 5.5-5.5S11 8 11 12z" fill="#c9a2a4"/></svg>John</div>
  <p>Neque porro quisquam est, qui dolorem ipsqu ia dolor sit amet, consectetur, adipisci.</p>
  <div class="more">READ MORE</div>
</div>
<div class="abs event" style="left:439px">
  <div class="pic" role="img" aria-label="Ribbon spools and paper on a workbench" style="background:linear-gradient(135deg,#e9e9ea,#c9c9cb 55%,#8d8e92)"></div>
  <h4>Finibus Bonorumet Maloru</h4>
  <div class="meta"><svg width="12" height="12" viewBox="0 0 12 12"><rect x="1" y="2" width="10" height="9" fill="none" stroke="#c9a2a4" stroke-width="1.4"/><path d="M1 5h10" stroke="#c9a2a4"/></svg>25/09/2017 &nbsp;| &nbsp;<svg width="11" height="12" viewBox="0 0 11 12"><circle cx="5.5" cy="3.5" r="2.8" fill="#c9a2a4"/><path d="M0 12c0-4 2-5.5 5.5-5.5S11 8 11 12z" fill="#c9a2a4"/></svg>John</div>
  <p>Neque porro quisquam est, qui dolorem ipsqu ia dolor sit amet, consectetur, adipisci.</p>
  <div class="more">READ MORE</div>
</div>
<div class="abs event" style="left:778px">
  <div class="pic" role="img" aria-label="Craftsperson working at a dusty studio table" style="background:linear-gradient(135deg,#4a3f3a,#b7775a 50%,#d8d4d0)"></div>
  <h4>Finibus Bonorumet Maloru</h4>
  <div class="meta"><svg width="12" height="12" viewBox="0 0 12 12"><rect x="1" y="2" width="10" height="9" fill="none" stroke="#c9a2a4" stroke-width="1.4"/><path d="M1 5h10" stroke="#c9a2a4"/></svg>25/09/2017 &nbsp;| &nbsp;<svg width="11" height="12" viewBox="0 0 11 12"><circle cx="5.5" cy="3.5" r="2.8" fill="#c9a2a4"/><path d="M0 12c0-4 2-5.5 5.5-5.5S11 8 11 12z" fill="#c9a2a4"/></svg>John</div>
  <p>Neque porro quisquam est, qui dolorem ipsqu ia dolor sit amet, consectetur, adipisci.</p>
  <div class="more">READ MORE</div>
</div>

<footer class="abs site-footer"></footer>
<div class="abs vrule" style="left:263px"></div>
<div class="abs vrule" style="left:507px"></div>
<div class="abs vrule" style="left:735px"></div>

<div class="abs foot-col" style="left:99px;color:#fff"><h5>Information</h5><ul><li>About Us</li><li>Careers</li><li>Privacy &amp; Security</li><li>Site Map</li><li>Terms of Use</li><li>Blog</li></ul></div>
<div class="abs foot-col" style="left:302px;color:#fff"><h5>Help &amp; support</h5><ul><li>Recommended Reading</li><li>Submit your Story</li><li>Contact Us</li><li>Frequently Asked Questions</li><li>How to Order</li></ul></div>
<div class="abs foot-col" style="left:550px;color:#fff"><h5>My Account</h5><ul><li>Delivery Information</li><li>My Account</li><li>Order Tracking</li><li>Reminder Service</li><li>Shipping, Returns &amp; Fees</li></ul></div>
<div class="abs foot-col" style="left:778px;color:#fff"><h5>Email Subscription</h5><p class="sub-text">Register your email address to get information about us</p></div>
<div class="abs sub-form"><div class="field">Email Address</div><div class="go">SUBSCRIBE</div></div>
<div class="abs stay" style="color:#fff">Stay Connected</div>
<div class="abs socials" aria-label="Social links"><span></span><span></span><span></span><span></span><span></span><span></span><span></span><span></span></div>
<div class="abs foot-rule"></div>
<p class="abs copy" style="color:#fff">Copyrights © 2017, ta belle vitrine. All Rights Reserved &nbsp;| &nbsp;Privacy Policy | Terms of Use | Feedback</p>

</body>
</html>
```